Spin Days 4 Fun business card

Spin Days 4 Fun is a national UK campaign that promotes the value of play for children. The website has recently undergone a redesign and will soon be going live, this business card design will need to reflect the new website's design and colour scheme, etc.
Key wording/info for inclusion (front)
- Strapline titles
A bit of Fun each morning (in caps)
giving you great free play ideas, everyday!
- Logo
Key wording for inclusion (rear)
- Download our free play app - Spin Days 4 Fun
- Visit our website - www.spindays4fun.co.uk
- To share hints and tips with other parents
www.facebook.com/spindaysforfun
- Want to get involved in the campaign? No matter who you are we would love to hear from you! Email - getinvolved@spindaysforfun.co.uk
Social media icons
Facebook facebook.com/spindays4fun
Twitter @spindays4fun
Youtube youtube.com/spindaysforfun
The target audience is parents of young children up to the age of 12.
Please note that all attached graphics are the property of the Northern Game & Craft Federation and must only be used for the purpose of this project.
Updates
Please note the design we are seeking will be in a business card 'shape' but will not be for a specific 'person' or name as such. We are looking for a colourful and modern design which is not 'corporate. Thank you.
Target Market(s)
Industry/Entity Type
Business
Look and feel

```html
<!DOCTYPE html>
<html lang="en">
<head>
<meta charset="utf-8">
<title>Spin Days 4 Fun – Business Card</title>
<link href="https://fonts.googleapis.com/css2?family=Montserrat:wght@400;600;700&family=Oswald:wght@500;600&display=swap" rel="stylesheet">
<style>
  :root {
    --canvas: #ece8e1;
    --card: #ffffff;
    --purple: #6a4ea3;
    --purple-dark: #523a85;
    --yellow: #ffdc2e;
    --green: #9ccc3c;
    --blue: #23b4e6;
    --pink: #e8497a;
    --ink: #3a3a3a;
    --on-purple: #ffffff;
  }
  * { box-sizing: border-box; margin: 0; padding: 0; }
  html, body { width: 1076px; height: 1200px; overflow: hidden; }
  body {
    background: var(--canvas);
    font-family: "Montserrat", Arial, sans-serif;
    color: var(--ink);
    position: relative;
  }
  .card {
    position: absolute;
    left: 118px;
    width: 840px;
    height: 480px;
    background: var(--card);
    box-shadow: 0 10px 28px rgba(0,0,0,.14);
    overflow: hidden;
  }
  .card--front { top: 70px; }
  .card--back { top: 650px; }

  .card__stripes { position: absolute; inset: 0; width: 100%; height: 100%; }

  .brand {
    position: absolute;
    display: flex;
    align-items: center;
    gap: 14px;
    font-weight: 700;
    color: var(--purple);
    white-space: nowrap;
  }
  .brand__dot {
    width: 30px; height: 30px; border-radius: 50%;
    background: var(--pink);
    flex: none;
  }
  .card--front .brand { left: 50%; top: 50%; transform: translate(-50%, -50%); font-size: 42px; }

  /* back */
  .back__panel {
    position: absolute; top: 0; right: 0; bottom: 0;
    width: 470px;
    background: var(--purple);
  }
  .back__bar { position: absolute; top: 0; bottom: 0; width: 14px; }
  .back__bar--blue { left: 348px; background: var(--blue); }
  .back__bar--green { left: 392px; background: var(--green); }

  .card--back .brand { left: 40px; top: 150px; font-size: 28px; }
  .brand__dot--small { width: 22px; height: 22px; }

  .icon-tile {
    width: 22px; height: 22px; flex: none;
    background: var(--yellow);
    border-radius: 3px;
    display: flex; align-items: center; justify-content: center;
  }
  .icon-tile svg { width: 14px; height: 14px; }
  .icon-tile--plain { width: 16px; height: 16px; border-radius: 2px; }

  .socials {
    position: absolute; left: 40px; bottom: 44px;
    list-style: none;
    font-size: 14px;
  }
  .socials li { display: flex; align-items: center; gap: 12px; margin-top: 10px; }

  .strapline {
    position: absolute; left: 450px; top: 50px;
    padding-left: 16px;
    border-left: 6px solid var(--yellow);
    color: var(--on-purple);
  }
  .strapline__title {
    font-family: "Oswald", "Arial Narrow", sans-serif;
    font-weight: 600; font-size: 26px; letter-spacing: 1px; line-height: 1.1;
    text-transform: uppercase;
  }
  .strapline__sub { font-size: 13px; font-weight: 400; margin-top: 6px; }

  .contacts {
    position: absolute; left: 468px; top: 168px;
    list-style: none;
    color: var(--on-purple);
  }
  .contacts li { display: flex; align-items: center; gap: 14px; margin-bottom: 16px; }
  .contacts__label {
    display: block;
    font-size: 10px; font-weight: 600; letter-spacing: 1.5px;
    text-transform: uppercase; color: var(--yellow);
  }
  .contacts__value { display: block; font-size: 14px; margin-top: 2px; }
</style>
</head>
<body>

<section class="card card--front" aria-label="Card front">
  <svg class="card__stripes" viewBox="0 0 840 480" aria-hidden="true">
    <polygon points="14,0 40,0 40,420 14,480" fill="var(--yellow)"/>
    <polygon points="40,0 46,0 46,414 40,420" fill="var(--purple)"/>
    <polygon points="826,480 800,480 800,60 826,0" fill="var(--yellow)"/>
    <polygon points="800,480 794,480 794,66 800,60" fill="var(--purple)"/>
  </svg>
  <div class="brand"><span class="brand__dot"></span>Spin Days 4 Fun</div>
</section>

<section class="card card--back" aria-label="Card back">
  <div class="back__panel"></div>
  <div class="back__bar back__bar--blue"></div>
  <div class="back__bar back__bar--green"></div>

  <div class="brand"><span class="brand__dot brand__dot--small"></span>Spin Days 4 Fun</div>

  <ul class="socials">
    <li><span class="icon-tile icon-tile--plain"></span>facebook.com/spindays4fun</li>
    <li><span class="icon-tile icon-tile--plain"></span>@spindays4fun</li>
    <li><span class="icon-tile icon-tile--plain"></span>youtube.com/spindaysforfun</li>
  </ul>

  <div class="strapline">
    <p class="strapline__title">A bit of Fun each morning</p>
    <p class="strapline__sub">giving you great free play ideas, everyday!</p>
  </div>

  <ul class="contacts">
    <li><span class="icon-tile"><svg viewBox="0 0 14 14" aria-hidden="true"><rect x="4" y="1" width="6" height="12" rx="1" fill="var(--purple-dark)"/></svg></span>
      <span><span class="contacts__label">Download our free play app</span><span class="contacts__value">Spin Days 4 Fun</span></span></li>
    <li><span class="icon-tile"><svg viewBox="0 0 14 14" aria-hidden="true"><circle cx="7" cy="7" r="5.5" stroke="var(--purple-dark)" stroke-width="1.5" fill="none"/><path d="M1.5 7h11M7 1.5c-2.5 3-2.5 8 0 11M7 1.5c2.5 3 2.5 8 0 11" stroke="var(--purple-dark)" stroke-width="1.2" fill="none"/></svg></span>
      <span><span class="contacts__label">Visit our website</span><span class="contacts__value">www.spindays4fun.co.uk</span></span></li>
    <li><span class="icon-tile"><svg viewBox="0 0 14 14" aria-hidden="true"><path d="M2 2h10v7H6l-3 3V9H2z" fill="var(--purple-dark)"/></svg></span>
      <span><span class="contacts__label">Share hints &amp; tips with other parents</span><span class="contacts__value">www.facebook.com/spindaysforfun</span></span></li>
    <li><span class="icon-tile"><svg viewBox="0 0 14 14" aria-hidden="true"><path d="M1 3h12v8H1z" fill="var(--purple-dark)"/><path d="M1 3l6 5 6-5" stroke="var(--yellow)" stroke-width="1.2" fill="none"/></svg></span>
      <span><span class="contacts__label">Want to get involved? Email</span><span class="contacts__value">getinvolved@spindaysforfun.co.uk</span></span></li>
  </ul>
</section>

</body>
</html>
```